Grafik/Logo für ein Schulungszertifikat DIN A4
Zielgruppe
Es soll nach einer Schulung für Social Media und Online Marketing für Unternehmer und Selbstständige ein Zertifikat auf dickerem Papier ausgehändigt werden.
Auf dieses sollen die Teilnehmer stolz sein ;-) und im Büro oder im Geschäft aufhängen wollen.
Das Logo des Zertifikates darf anschließend auch alleinstehend auf der Homepage der Unternehmensseiten von Teilnehmern verwendet werden dürfen.
Es soll eine Gemeinschaft symbolisiert werden. Denn bei dieser Schulung schulen Unternehmer aus dem Bereich Onlinemarketing andere Unternehmer aus unterschiedlichsten Branchen und Bereichen. Eben aus allen, in denen Onlinemarketing und Social Media sinnvoll eingesetzt werden kann.
Die Inhalte können Sie dem beigefügten Dokument entnehmen.
Aufgabenstellung
Es werden benötigt:
1. Ein Logo/Zertifikatssiegel (auffälig sein und ins Auge fallen, ob online oder wenn das an der Wand hängt, oder als Autoaufkleber genutzt wird)
2. Layout für das DIN A 4 Zertifikat mit dem Zertifikatssiegel

```html
<!DOCTYPE html>
<html lang="de">
<head>
<meta charset="utf-8">
<title>Zertifikat – Social Media und Online Marketing</title>
<link rel="stylesheet" href="https://fonts.googleapis.com/css2?family=Fira+Sans:wght@400;500;700&family=Fira+Sans+Condensed:wght@500;700&display=swap">
<style>
  :root {
    --teal: #3a98a6;
    --teal-dark: #1f6a77;
    --teal-deep: #17525d;
    --line-light: #a9d3da;
    --text: #58595b;
    --heading: #4e4f51;
    --paper: #ffffff;
    --red: #d42a2f;
    --orange: #ec6a3c;
    --silver-light: #dfe2e5;
    --silver: #a9aeb3;
  }
  html, body { margin: 0; padding: 0; overflow: hidden; background: var(--paper); }
  .certificate {
    position: relative;
    width: 849px; height: 1200px;
    background: var(--paper);
    font-family: "Fira Sans", Arial, sans-serif;
    color: var(--text);
    overflow: hidden;
  }
  .header {
    position: absolute; left: 0; top: 0; width: 849px; height: 375px;
    background: var(--teal);
  }
  .header__top-strip { position: absolute; left: 0; top: 0; width: 100%; height: 11px; background: var(--teal-dark); }
  .header__band {
    position: absolute; left: 0; top: 330px; width: 100%; height: 42px;
    background: linear-gradient(to bottom, var(--teal-dark), var(--teal-deep));
    border-top: 3px solid var(--line-light);
  }
  .brand { position: absolute; left: 0; top: 40px; width: 100%; text-align: center; color: #fff; }
  .brand__name { font-size: 46px; font-weight: 400; line-height: 1; letter-spacing: 0.5px; }
  .brand__tagline { margin-top: 56px; font-size: 15px; font-weight: 400; line-height: 1; }
  .header__title {
    position: absolute; left: 0; top: 206px; width: 100%; margin: 0; text-align: center;
    color: #fff; font-size: 106px; font-weight: 700; letter-spacing: 9px; line-height: 1;
  }
  .recipient {
    position: absolute; left: 0; top: 418px; width: 100%; text-align: center;
    font-size: 46px; font-weight: 700; color: var(--heading);
  }
  .centered { position: absolute; left: 0; width: 100%; text-align: center; font-size: 17px; }
  .period-intro { top: 514px; }
  .period { top: 536px; font-weight: 700; color: #3f4042; }
  .seminar-intro { top: 588px; }
  .seminar-title { top: 610px; font-size: 36px; font-weight: 700; color: var(--heading); }
  .statement {
    position: absolute; left: 124px; top: 676px; width: 600px; margin: 0;
    font-size: 17px; line-height: 25px;
  }
  .place-date { position: absolute; left: 124px; top: 796px; font-size: 18px; margin: 0; }
  .signature { position: absolute; top: 868px; }
  .signature--left { left: 124px; }
  .signature--right { left: 339px; }
  .signature__name { font-size: 17px; font-weight: 400; color: #444; }
  .signature__role { margin-top: 10px; font-family: "Fira Sans Condensed", Arial, sans-serif; font-size: 10px; font-weight: 700; color: #444; }
  .topics {
    position: absolute; left: 124px; top: 984px; margin: 0;
    font-family: "Fira Sans Condensed", "Arial Narrow", sans-serif;
    font-size: 10.5px; line-height: 13.8px; font-weight: 500; color: #3c3c3c;
  }
  .topics__heading { font-weight: 700; }
  .topics ul { list-style: none; margin: 0; padding: 0; }
  .seal { position: absolute; left: 570px; top: 858px; width: 226px; height: 226px; }
  .footer-bar {
    position: absolute; left: 0; top: 1158px; width: 100%; height: 22px;
    background: linear-gradient(to right, #c4161c, var(--red) 20%, var(--orange) 50%, var(--red) 80%, #c4161c);
  }
</style>
</head>
<body>
<main class="certificate">
  <header class="header">
    <div class="header__top-strip"></div>
    <div class="brand">
      <div class="brand__name">Klarwerk Media</div>
      <div class="brand__tagline">Kommunikationsagentur • Social Media</div>
    </div>
    <h1 class="header__title">ZERTIFIKAT</h1>
    <div class="header__band"></div>
  </header>

  <div class="recipient">Vorname Nachname</div>
  <div class="centered period-intro">hat in der Zeit von</div>
  <div class="centered period">1. November bis 23. Dezember 2014</div>
  <div class="centered seminar-intro">das Seminar</div>
  <div class="centered seminar-title">Social Media und Online Marketing</div>
  <p class="statement">absolviert und seine fachliche Kompetenz und die praxisgerechte Umset-<br>zung im Rahmen einer Abschlussprüfung erfolgreich nachgewiesen.</p>

  <p class="place-date">Dortmund, den 8. Januar 2015</p>

  <div class="signature signature--left">
    <div class="signature__name">Lena Hartwig</div>
    <div class="signature__role">Geschäftsführerin</div>
  </div>
  <div class="signature signature--right">
    <div class="signature__name">Vorname Nachname</div>
    <div class="signature__role">Lehrgangsleiter</div>
  </div>

  <div class="topics">
    <div class="topics__heading">Themenschwerpunkte:</div>
    <ul>
      <li>Die Website: „Das Herz im Social Business“</li>
      <li>Suchmaschinenoptimierung und Linkbuilding</li>
      <li>Blog und Blogredaktion</li>
      <li>Internetrecht/ Social Media-Recht</li>
      <li>Facetown – Grundlagen und Einbindung in Kommunikationsstrategien</li>
      <li>Jobnetz</li>
      <li>Chirpline und Circlo+</li>
      <li>Monitoring</li>
      <li>Findr Ads, Findr Dienste und Findr Analytics</li>
    </ul>
  </div>

  <svg class="seal" viewBox="0 0 226 226" role="img" aria-label="Platz für das Zertifikatssiegel">
    <defs>
      <radialGradient id="seal-fill" cx="40%" cy="35%" r="70%">
        <stop offset="0" stop-color="var(--silver-light)"/>
        <stop offset="1" stop-color="var(--silver)"/>
      </radialGradient>
    </defs>
    <circle cx="113" cy="113" r="112" fill="url(#seal-fill)"/>
  </svg>

  <div class="footer-bar"></div>
</main>
</body>
</html>
```